A private security company called "Tavron Security Services Ltd"

Hello everybody,

We need a web page for a company based in NZ. It is mainly an informative website so it would be wonderful if the designer puts their absolute best into making it a website that I would really appreciate. The website needs to show professionalism and also needs to make our web surfers find the information they need in a click. the company's colour is black and silver, and if those two colours could be integrated into the website it would be absolutely lovely. Please do contact me for any information.

Sincerely,
Dorian Vaskel

Industry/Entity Type

Security

```html
<!DOCTYPE html>
<html lang="en">
<head>
<meta charset="utf-8">
<title>Tavron Security Services Ltd</title>
<link href="https://fonts.googleapis.com/css2?family=Open+Sans:wght@300;400;600&display=swap" rel="stylesheet">
<style>
:root{
  --ink:#333;
  --muted:#666;
  --soft:#888;
  --line:#dcdcdc;
  --black:#111;
  --tile-1:#222;
  --tile-2:#2e2e2e;
  --tile-3:#3b3b3b;
  --footer:#4a4a4a;
  --footer-line:#5c5c5c;
  --bottom:#333;
  --accent:#29b6d6;
  --phone:#e8a33a;
  --white:#fff;
}
*{margin:0;padding:0;box-sizing:border-box}
html,body{width:974px;height:1200px;overflow:hidden;background:var(--white)}
body{font-family:'Open Sans',Arial,sans-serif;color:var(--ink);position:relative}
.abs{position:absolute}
ul{list-style:none}

/* hero */
.hero-photo{left:0;top:0;width:974px;height:484px;
  background:linear-gradient(100deg,#dfe6f5 0%,#c5d3ee 35%,#a8bde6 60%,#8ea9d9 75%,#b9b3a9 82%,#9f9a93 100%)}
.header{left:89px;top:25px;width:796px;height:83px;background:rgba(255,255,255,.93);box-shadow:0 1px 3px rgba(0,0,0,.15)}
.brand{left:18px;top:22px;display:flex;align-items:center;gap:8px}
.brand-mark{width:12px;height:12px;background:var(--black)}
.brand-name{font-size:11px;font-weight:600;color:var(--black);line-height:14px;letter-spacing:.5px;text-transform:uppercase}
.nav{left:0;top:34px;width:796px;height:16px;font-size:11.5px;color:var(--muted);text-transform:uppercase}
.nav span{position:absolute;white-space:nowrap}
.hero-title{left:113px;top:156px;font-size:32px;font-weight:600;color:#333;line-height:42px}
.hero-sub{left:112px;top:196px;font-size:32px;font-weight:300;color:#333;line-height:40px}
.hero-copy{left:112px;top:240px;font-size:10.5px;line-height:17px;color:#555;width:340px}
.btn-learn{left:113px;top:285px;height:30px;width:106px}
.btn-learn span{position:absolute;left:14px;top:7px;font-size:12px;color:var(--white);font-weight:400}

/* service tiles */
.tile{top:364px;height:120px;color:var(--white)}
.tile h3{position:absolute;left:40px;top:23px;font-size:22px;font-weight:400;white-space:nowrap}
.tile p{position:absolute;left:40px;top:59px;font-size:11.5px;line-height:13px;font-weight:300;width:200px}
.t1{left:92px;width:263px;background:var(--tile-1)}
.t2{left:355px;width:264px;background:var(--tile-2)}
.t2 h3,.t2 p{left:40px}
.t3{left:619px;width:265px;background:var(--tile-3)}

/* content */
.heading{font-size:22px;font-weight:300;color:#222;white-space:nowrap;line-height:28px}
.bullets li{position:absolute;left:0;font-size:11.5px;color:var(--ink);white-space:nowrap;line-height:14px}
.bullets li::before{content:"";position:absolute;left:-19px;top:7px;width:4px;height:4px;border-radius:50%;background:var(--black)}
.bullets.links li{color:var(--muted);text-decoration:underline;text-decoration-color:#999}
.tag-btn{background:var(--black);color:var(--white);font-size:10.5px;line-height:18px;height:18px;padding:0 5px;white-space:nowrap}
.rule-h{height:1px;background:var(--line)}
.rule-v{width:1px;background:var(--line)}
.address{left:209px;top:851px;font-size:11px;line-height:17.5px;color:var(--soft);font-weight:300}
.send-btn{left:207px;top:918px;width:98px;height:20px;border:1px solid var(--line);font-size:10.5px;line-height:18px;padding-left:17px;color:#222}
.welcome-copy{left:386px;top:558px;width:470px;font-size:18px;line-height:24.5px;font-weight:300;color:#444}
.welcome-copy .accent{color:var(--accent)}
.staff-photo{left:614px;top:728px;width:197px;height:74px;background:linear-gradient(90deg,#8e8f8d,#cfd2d4 45%,#7d7b78 70%,#b9ad9a)}
.staff-caption{left:615px;top:814px;font-size:13px;color:var(--muted);text-decoration:underline;white-space:nowrap}
.staff-copy{left:615px;top:840px;width:205px;font-size:11.5px;line-height:14.6px;color:#444}

/* footer */
.footer{left:0;top:980px;width:974px;height:177px;background:var(--footer);color:var(--white)}
.footer .heading{color:var(--white)}
.info-col li{font-size:11px;line-height:17px;color:#eee;padding-left:11px;position:relative;white-space:nowrap}
.info-col li::before{content:"";position:absolute;left:1px;top:6px;border-left:3px solid #ddd;border-top:2.5px solid transparent;border-bottom:2.5px solid transparent}
.email-label{left:675px;top:64px;font-size:10px;color:#eee;letter-spacing:.2px}
.email-field{left:675px;top:92px;width:181px;height:16px;border-radius:8px;background:var(--white)}
.subscribe{left:675px;top:121px;width:73px;height:17px;border-radius:9px;background:var(--black);font-size:10.5px;line-height:17px;text-align:center;font-weight:600}
.bottom-bar{left:0;top:1157px;width:974px;height:43px;background:var(--bottom);color:#eee;font-size:10.5px}
.bottom-bar a{color:#eee}
.phone{color:var(--phone)}
</style>
</head>
<body>

<div class="abs hero-photo" role="img" aria-label="Photo of a wall-mounted security camera against a blue sky"></div>

<header class="abs header">
  <div class="abs brand">
    <span class="brand-mark"></span>
    <div class="brand-name">Tavron<br>Security Services Ltd</div>
  </div>
  <nav class="abs nav">
    <span style="left:224px">Home</span>
    <span style="left:285px">About Us</span>
    <span style="left:366px">Security System</span>
    <span style="left:488px">Specialized Security</span>
    <span style="left:634px">Carrers</span>
    <span style="left:709px">Contact Us</span>
  </nav>
</header>

<h1 class="abs hero-title">Newzealand’s Best</h1>
<h2 class="abs hero-sub">Security Company</h2>
<p class="abs hero-copy">Lorem ipsum dolor sit amet, consectetur adipisicing elit, sed do eiusmod tempor incididunt dolore magna aliqua..</p>
<div class="abs btn-learn">
  <svg width="106" height="30" viewBox="0 0 106 30"><path d="M0 0H93L106 15L93 30H0Z" fill="#111"/></svg>
  <span>Learn More</span>
</div>

<section class="abs tile t1"><h3>Property Guards</h3><p>The standard chunk of Lorem Ipsum used since the 1500s</p></section>
<section class="abs tile t2"><h3>Security Consultancy</h3><p>The standard chunk of Lorem Ipsum used since the 1500s</p></section>
<section class="abs tile t3"><h3>Private Investigation</h3><p>The standard chunk of Lorem Ipsum used since the 1500s</p></section>

<!-- left column -->
<h3 class="abs heading" style="left:129px;top:514px">featured services</h3>
<ul class="abs bullets" style="left:151px;top:0">
  <li style="top:567px">taserto yasers mertase</li>
  <li style="top:592px">taserto yasers mertase</li>
  <li style="top:617px">taserto yasers mertase</li>
  <li style="top:659px">taserto yasers mertase</li>
  <li style="top:684px">taserto yasers yard soul mertase</li>
  <li style="top:708px">serto yasers mertase</li>
  <li style="top:733px">taserto mertase</li>
</ul>
<div class="abs tag-btn" style="left:131px;top:765px">read more</div>
<div class="abs rule-h" style="left:130px;top:799px;width:187px"></div>
<h3 class="abs heading" style="left:129px;top:820px">featured services</h3>
<svg class="abs" style="left:130px;top:859px" width="62" height="44" viewBox="0 0 62 44">
  <rect x="1" y="1" width="60" height="42" fill="none" stroke="#ccc" stroke-width="2"/>
  <path d="M2 2L31 25L60 2M2 42L24 20M60 42L38 20" fill="none" stroke="#ccc" stroke-width="2"/>
</svg>
<p class="abs address">24 Harbour Lane<br>Level Two, Wellington<br>NZ 6011</p>
<div class="abs send-btn">
  <svg class="abs" style="left:8px;top:7px" width="4" height="6"><path d="M0 0L4 3L0 6Z" fill="#222"/></svg>
  send message
</div>
<div class="abs rule-v" style="left:354px;top:519px;height:224px"></div>

<!-- welcome -->
<h2 class="abs heading" style="left:383px;top:514px;font-size:25px;line-height:32px">Welcome!</h2>
<p class="abs welcome-copy">The standard chunk of Lorem Ipsum used since the 1500s "Lorem ipsum dolor sit amet, <span class="accent">consectetur</span> adipisic­ing elit.</p>
<div class="abs rule-h" style="left:388px;top:658px;width:466px"></div>

<h3 class="abs heading" style="left:385px;top:679px">featured services</h3>
<ul class="abs bullets links" style="left:407px;top:0">
  <li style="top:732px">taserto yasers mertase</li>
  <li style="top:757px">yasers mertase</li>
  <li style="top:782px">taserto yasers mertase</li>
  <li style="top:806px">taserto mertase</li>
  <li style="top:832px">taserto yasers mertase</li>
</ul>
<div class="abs tag-btn" style="left:383px;top:873px">view more</div>
<div class="abs rule-v" style="left:581px;top:688px;height:225px"></div>

<h3 class="abs heading" style="left:613px;top:679px">our staff</h3>
<div class="abs staff-photo" role="img" aria-label="Photo of three staff members working together in an office"></div>
<a class="abs staff-caption">Base dolar yasers mertase</a>
<p class="abs staff-copy">Lorem ipsum dolor sit amet, consecte­tur adipisicing elit, sed do minim veniam, quis nostrud exercitation</p>

<!-- footer -->
<footer class="abs footer">
  <h3 class="abs heading" style="left:130px;top:21px">useful info</h3>
  <ul class="abs info-col" style="left:131px;top:63px">
    <li>Lorem ipsum dolor</li><li>Sit amet consectetur</li><li>adipsicing elit</li>
  </ul>
  <ul class="abs info-col" style="left:311px;top:63px">
    <li>Sed do euismod</li><li>tempor incidunt</li>
  </ul>
  <ul class="abs info-col" style="left:490px;top:63px">
    <li>Magna Aliqua</li><li>What we do</li>
  </ul>
  <div class="abs" style="left:638px;top:17px;width:1px;height:143px;background:var(--footer-line)"></div>
  <h3 class="abs heading" style="left:675px;top:22px">newsletter sign up</h3>
  <div class="abs email-label">ENTER YOUR E-MAIL</div>
  <div class="abs email-field"></div>
  <div class="abs subscribe">Subscribe</div>
</footer>

<div class="abs bottom-bar">
  <span class="abs" style="left:141px;top:14px">TAVRON 2014 &nbsp;| &nbsp;<a>Privacy policy</a></span>
  <span class="abs" style="right:138px;top:14px">Call Free: <span class="phone">1 800-555-0142</span></span>
</div>

</body>
</html>
```